Quillmarsh Property Solutions need a business card design

Hello guys. We would need a business card design asap please.
We are a start up property investment business based in London UK specialised in buying, selling, managing and letting properties and helping distressed property owners.
The name of our Business is Quillmarsh, the logo symbolises the four fundamental elements of the world (earth, air, fire and water) and so it stands for strength, stability, longevity.
We would like the business card to communicate professionalism and reliability. Many many thanks indeed for your work.

Details:

1.) Rosalind Updike
Property Investor
Mobile: +44(0)7700123456
Email: rosalind.quillmarsh@mailbox-example.com

2.) Dominic Updike
Property Investor
Mobile: +44(0)7700987654
Email: dominic.quillmarsh@mailbox-example.com

```html
<!DOCTYPE html>
<html lang="en">
<head>
<meta charset="utf-8">
<title>Quillmarsh Property Solutions – Business Card</title>
<link href="https://fonts.googleapis.com/css2?family=Open+Sans:wght@400;600;700&display=swap" rel="stylesheet">
<style>
  :root {
    --page-bg: #e6e7ec;
    --card-white: #ffffff;
    --brand-green: #1dbf5c;
    --brand-red: #e3222f;
    --text-grey: #8c8c8c;
    --text-dark: #333a40;
    --icon-blue: #2a6fd6;
  }
  * { box-sizing: border-box; margin: 0; padding: 0; }
  html, body {
    width: 1200px; height: 987px; overflow: hidden;
    background: var(--page-bg);
    font-family: "Open Sans", Arial, sans-serif;
  }
  .canvas { position: relative; width: 1200px; height: 987px; }
  .card {
    position: absolute; left: 220px;
    width: 760px; height: 434px;
    border-radius: 34px; overflow: hidden;
    box-shadow: 0 6px 18px rgba(0,0,0,0.12);
  }
  .card--front { top: 36px; background: var(--card-white); }
  .card--back { top: 516px; background: var(--brand-red); }

  .front-swoosh { position: absolute; inset: 0; width: 100%; height: 100%; }

  .brand {
    position: absolute; left: 56px; top: 168px;
    display: flex; align-items: center; gap: 14px;
  }
  .brand__mark { width: 26px; height: 26px; background: var(--brand-green); flex: none; }
  .brand__name {
    font-weight: 700; font-size: 20px; letter-spacing: 1px;
    text-transform: uppercase; color: var(--text-grey);
    line-height: 1.25;
  }
  .brand__name span { display: block; }

  .contact {
    position: absolute; left: 56px; top: 282px;
    list-style: none; display: flex; flex-direction: column; gap: 10px;
  }
  .contact__item {
    display: flex; align-items: center; gap: 12px;
    font-size: 16px; color: var(--text-dark);
  }
  .contact__icon { width: 18px; height: 18px; flex: none; }

  .holder {
    position: absolute; right: 40px; top: 250px; text-align: right;
    color: #fff;
  }
  .holder__name { font-weight: 700; font-size: 28px; line-height: 1.2; white-space: nowrap; }
  .holder__role { font-weight: 400; font-size: 20px; }

  .back-content {
    position: absolute; inset: 0;
    display: flex; flex-direction: column; align-items: center; justify-content: center;
    gap: 22px; color: #fff;
  }
  .back-brand { display: flex; align-items: center; gap: 16px; }
  .back-brand__mark { width: 36px; height: 36px; background: #fff; }
  .back-brand__name {
    font-weight: 700; font-size: 36px; letter-spacing: 2px; text-transform: uppercase;
  }
  .back-web { font-size: 22px; letter-spacing: 3px; }
</style>
</head>
<body>
<main class="canvas">

  <section class="card card--front" aria-label="Business card front">
    <svg class="front-swoosh" viewBox="0 0 760 434" aria-hidden="true">
      <path d="M0,0 L760,0 L760,434 L540,434 C420,160 260,22 0,22 Z" fill="var(--brand-green)"/>
      <path d="M0,40 C245,40 392,172 514,434" fill="none" stroke="var(--brand-red)" stroke-width="10"/>
    </svg>

    <div class="brand">
      <span class="brand__mark"></span>
      <p class="brand__name"><span>Quillmarsh</span><span>Property Solutions</span></p>
    </div>

    <ul class="contact">
      <li class="contact__item">
        <svg class="contact__icon" viewBox="0 0 18 18" aria-hidden="true">
          <rect x="4" y="1" width="10" height="16" rx="2" fill="var(--icon-blue)"/>
          <rect x="6" y="3.5" width="6" height="8" fill="#fff"/>
        </svg>
        <span>+44(0)7700123456</span>
      </li>
      <li class="contact__item">
        <svg class="contact__icon" viewBox="0 0 18 18" aria-hidden="true">
          <rect x="1" y="4" width="16" height="11" rx="1.5" fill="var(--icon-blue)"/>
          <path d="M1.5,5 L9,10.5 L16.5,5" fill="none" stroke="#fff" stroke-width="1.4"/>
        </svg>
        <span>rosalind.quillmarsh@mailbox-example.com</span>
      </li>
    </ul>

    <div class="holder">
      <p class="holder__name">Rosalind Updike</p>
      <p class="holder__role">Property Investor</p>
    </div>
  </section>

  <section class="card card--back" aria-label="Business card back">
    <div class="back-content">
      <div class="back-brand">
        <span class="back-brand__mark"></span>
        <span class="back-brand__name">Quillmarsh</span>
      </div>
      <p class="back-web">www.quillmarsh-example.com</p>
    </div>
  </section>

</main>
</body>
</html>
```